BUSINESS CARD - HALLORAN FIELD SERVICES

I would like to create a business card for my fertilizer spreading business. I would like to incorporate my existing logo and also a description of the services offered. The business card will be given to farmers so must be kept simple but effective. It will also be left in stores so much also be eye catching in order to stand out from other cards.

Target Market(s)

FARMERS

Requirements
Must have
• FRONT OF CARD = EXISTING LOGO + "CUSTOMISED SPREADING" below the logo

REAR Of CARD = SERVICES OFFERED AND CONTACT DETAILS

- Bulk fertilizer including Lime, Gypsum, Manure & Compost
- Granular fertilizer including Single Super, Urea, Terra-N, & Custom Blends
- Modern equipment - Autosteer & Variable Rate Capable
- Friendly & Reliable Service
- Contact Gus: 0417 552 308
Nice to have
• utilize same color scheme as existing logo

```html
<!DOCTYPE html>
<html lang="en">
<head>
<meta charset="utf-8">
<title>Halloran Field Services – Business Card</title>
<link rel="stylesheet" href="https://fonts.googleapis.com/css2?family=Roboto:wght@400;500;700&family=Exo+2:wght@700&display=swap">
<style>
  :root {
    --page-bg: #d6d6d6;
    --card-grey: #58585a;
    --card-white: #ffffff;
    --accent-orange: #f7941d;
    --text-light: #ffffff;
    --text-dark: #58585a;
  }
  * { box-sizing: border-box; margin: 0; padding: 0; }
  html, body {
    width: 1200px; height: 801px; overflow: hidden;
    background: var(--page-bg);
    font-family: "Roboto", Arial, sans-serif;
  }
  .card {
    position: absolute; top: 274px;
    width: 443px; height: 263px; overflow: hidden;
  }
  .card--rear { left: 153px; background: var(--card-grey); }
  .card--front { left: 625px; background: var(--card-white); }

  .rear-artwork {
    position: absolute; left: 0; top: 0; width: 225px; height: 263px;
    background: linear-gradient(135deg, #ffffff 0%, #ececec 45%, #8a8a8c 100%);
    border-bottom-right-radius: 100% 100%;
  }

  .contact {
    position: absolute; right: 23px; top: 60px;
    display: flex; align-items: center; gap: 4px;
    color: var(--text-light); font-size: 19px; line-height: 1;
  }
  .contact__icon { width: 21px; height: 21px; }
  .contact__name { font-weight: 700; }

  .services {
    position: absolute; right: 16px; top: 108px;
    list-style: none; text-align: right;
    color: var(--text-light); font-size: 13.4px; line-height: 15px;
  }
  .services__item {
    position: relative; padding-right: 14px; margin-bottom: 4px;
  }
  .services__item::after {
    content: ""; position: absolute; right: 0; top: 4px;
    width: 8px; height: 8px; border-radius: 50%;
    background: var(--accent-orange);
  }

  .brand {
    position: absolute; left: 0; right: 0; top: 50px;
    display: flex; flex-direction: column; align-items: center; gap: 10px;
  }
  .brand__mark {
    width: 100px; height: 100px; border-radius: 50%;
    background: var(--text-dark);
  }
  .brand__name {
    color: var(--text-dark); font-weight: 700; font-size: 24px; letter-spacing: 0.3px; line-height: 1.1;
  }
  .tagline-band {
    position: absolute; left: 0; bottom: 0; width: 100%; height: 44px;
    background: var(--card-grey);
    display: flex; align-items: center; justify-content: center;
  }
  .tagline {
    font-family: "Exo 2", "Roboto", sans-serif; font-weight: 700;
    font-size: 20px; color: var(--accent-orange); letter-spacing: 0.4px;
  }
</style>
</head>
<body>
  <section class="card card--rear">
    <div class="rear-artwork" role="img" aria-label="Livestock silhouettes with a growing sprout in grey, white and orange"></div>

    <div class="contact">
      <svg class="contact__icon" viewBox="0 0 24 24" aria-hidden="true">
        <circle cx="12" cy="12" r="10.5" fill="none" stroke="var(--accent-orange)" stroke-width="1.5"/>
        <path d="M8.5 6.5l2 2.2-1.1 1.6c.7 1.6 1.9 2.8 3.4 3.5l1.6-1.1 2.2 2-1.2 1.8c-3.9-.4-7.5-4-7.9-7.9z" fill="var(--accent-orange)"/>
      </svg>
      <span><span class="contact__name">Gus:</span> 0417 552 308</span>
    </div>

    <ul class="services">
      <li class="services__item">Bulk fertilizer including Lime<br>Gypsum, Manure &amp; Compost</li>
      <li class="services__item">Granular fertilizer including<br>Single Super, Urea, Terra-N<br>Custom Blends</li>
      <li class="services__item">Modern equipment</li>
      <li class="services__item">Autosteer &amp; Variable Rate Capable</li>
      <li class="services__item">Friendly &amp; Reliable Service</li>
    </ul>
  </section>

  <section class="card card--front">
    <div class="brand">
      <div class="brand__mark" aria-hidden="true"></div>
      <h1 class="brand__name">HALLORAN FIELD SERVICES</h1>
    </div>
    <div class="tagline-band">
      <p class="tagline">CUSTOMISED SPREADING</p>
    </div>
  </section>
</body>
</html>
```